Request for Business Card Design

Hi. My name is Marlene, I am looking for a new business card design for my company, Quarrow Signal Instruments, LLC. I really like the design you did for Tarsel Venture and was hoping you could do something similar using our full logo and our mark. I am also open to any raised texture design using our mark. I have attached our full logo, which would need to be somewhere on the card, as well as the mark in both outline and full form, as well as our brand colors / guide. The card does not have to be white, as long as our logo and mark appear. I actually like darker colored business cards more, but am open to all options. If you are interested in working with me, please let me know. We would also take the business card design into letterhead design if you can do that.

```html
<!DOCTYPE html>
<html lang="en">
<head>
<meta charset="utf-8">
<title>Quarrow Signal Instruments — Business Card</title>
<link href="https://fonts.googleapis.com/css2?family=Barlow+Condensed:ital,wght@0,500;0,700;1,600&family=Arimo:wght@400&display=swap" rel="stylesheet">
<style>
  :root {
    --stage: #0e0e0f;
    --card: #232324;
    --card-deep: #1b1b1c;
    --pattern-light: #2c2c2d;
    --pattern-dark: #171718;
    --brand-blue: #0a8db3;
    --ink-light: #f1f1f1;
    --ink-soft: #c9c9c9;
    --divider: #5a5a5c;
  }
  * { box-sizing: border-box; margin: 0; padding: 0; }
  html, body {
    width: 1200px; height: 963px; overflow: hidden;
    background: var(--stage);
  }
  .sheet {
    width: 1200px; height: 963px;
    display: flex; align-items: center; justify-content: center;
    gap: 40px;
  }
  .card {
    position: relative;
    width: 540px; height: 309px;
    border-radius: 22px;
    background: var(--card);
    box-shadow: 0 5px 0 var(--brand-blue), 0 18px 40px rgba(0,0,0,.6);
    overflow: hidden;
  }

  /* Front: raised texture field with logo */
  .card-front .texture-field {
    position: absolute; inset: 0;
    background: radial-gradient(ellipse at 40% 60%, var(--pattern-light), var(--pattern-dark));
  }
  .brand-lockup {
    position: absolute; left: 150px; top: 112px;
    display: flex; align-items: center; gap: 16px;
  }
  .brand-dot {
    width: 58px; height: 58px; border-radius: 50%;
    background: var(--brand-blue);
    flex: none;
  }
  .brand-name {
    font-family: "Barlow Condensed", sans-serif;
    font-weight: 700;
    color: var(--ink-light);
    text-transform: uppercase;
    line-height: 1;
  }
  .brand-name .primary { display: block; font-size: 50px; letter-spacing: 4px; }
  .brand-name .secondary { display: block; font-size: 15px; letter-spacing: 1.6px; margin-top: 4px; }

  /* Back: contact details */
  .card-back {
    background: linear-gradient(160deg, var(--card) 0%, var(--card-deep) 100%);
  }
  .identity {
    position: absolute; right: 282px; top: 96px;
    text-align: right;
  }
  .person-name {
    font-family: "Barlow Condensed", sans-serif;
    font-style: italic; font-weight: 600;
    font-size: 38px; line-height: 1;
    color: var(--brand-blue);
    text-transform: uppercase;
    letter-spacing: -0.5px;
  }
  .person-role {
    font-family: "Arimo", sans-serif;
    font-size: 16px; color: var(--ink-light);
    margin-top: 6px;
  }
  .split-rule {
    position: absolute; left: 270px; top: 118px;
    width: 1px; height: 66px;
    background: var(--divider);
  }
  .contact-list {
    position: absolute; left: 288px; top: 122px;
    list-style: none;
    font-family: "Arimo", sans-serif;
    font-size: 15px; color: var(--ink-light);
  }
  .contact-list li {
    display: flex; align-items: center; gap: 9px;
    height: 20px;
  }
  .contact-list svg { width: 13px; height: 13px; flex: none; }
  .address {
    position: absolute; left: 0; right: 0; top: 222px;
    text-align: center;
    font-family: "Arimo", sans-serif;
    font-size: 15px; color: var(--ink-light);
  }
</style>
</head>
<body>
  <main class="sheet">

    <section class="card card-front">
      <div class="texture-field" role="img" aria-label="Raised repeating brand-mark texture across the card surface"></div>
      <div class="brand-lockup">
        <span class="brand-dot"></span>
        <p class="brand-name">
          <span class="primary">Quarrow</span>
          <span class="secondary">Signal Instruments</span>
        </p>
      </div>
    </section>

    <section class="card card-back">
      <div class="identity">
        <h1 class="person-name">Elias Varnholt</h1>
        <p class="person-role">Manager</p>
      </div>
      <div class="split-rule"></div>
      <ul class="contact-list">
        <li>
          <svg viewBox="0 0 24 24" fill="none" stroke="var(--brand-blue)" stroke-width="2.4" stroke-linecap="round" stroke-linejoin="round"><path d="M5 3h4l2 5-2.5 1.5a11 11 0 0 0 6 6L16 13l5 2v4a2 2 0 0 1-2 2A16 16 0 0 1 3 5a2 2 0 0 1 2-2z"/></svg>
          555-014-2100
        </li>
        <li>
          <svg viewBox="0 0 24 24" fill="none" stroke="var(--brand-blue)" stroke-width="2.4" stroke-linejoin="round"><rect x="2" y="5" width="20" height="14" rx="1"/><path d="M2 6l10 7 10-7"/></svg>
          hello@quarrowsignal.com
        </li>
        <li>
          <svg viewBox="0 0 24 24" fill="none" stroke="var(--brand-blue)" stroke-width="2.2"><circle cx="12" cy="12" r="10"/><path d="M2 12h20M12 2c3 3 3 17 0 20M12 2c-3 3-3 17 0 20"/></svg>
          www.quarrowsignal.com
        </li>
      </ul>
      <p class="address">Your Address, City, State, Zip 0000</p>
    </section>

  </main>
</body>
</html>
```